Private lender of mortgages and rent to own housing

need a website that reflects real estate especially mortgage lending and rent to own houses..
Sections as follows
Home About Types of mortgages Rent to own Contact us
Target Market(s)
consumers who require non traditonal mortgages
Industry/Entity Type
Mortgage
Coding
Coded - Design and coding required
Number of Pages Required
4 page
Font styles to use
Sans Serif
Colors
Designer to choose colors to be used in the design.
Requirements
Must have
- background pictures on pages. with nice picture on homepage of houses or a community
Nice to have
- contact us form i supplied a ink to

```html
<!DOCTYPE html>
<html lang="en">
<head>
<meta charset="utf-8">
<title>Northfield Lending Group</title>
<link href="https://fonts.googleapis.com/css2?family=Questrial&family=Montserrat:wght@700&display=swap" rel="stylesheet">
<style>
:root{
  --navy:#27215f;
  --navy-dark:#17134a;
  --ink:#333333;
  --muted:#555555;
  --band:#f5f5f5;
  --white:#ffffff;
  --footer-text:#d9d8ea;
  --hero-a:#b3b1cf;
  --hero-b:#7f7caa;
}
*{margin:0;padding:0;box-sizing:border-box}
html,body{width:734px;height:1200px;overflow:hidden;background:var(--white)}
body{position:relative;font-family:"Questrial",sans-serif;color:var(--ink)}
.site-header{position:absolute;left:0;top:0;width:734px;height:68px;background:var(--white);box-shadow:0 2px 3px rgba(0,0,0,.25);z-index:3}
.brand{position:absolute;left:60px;top:38px;display:flex;align-items:center;gap:6px;font-size:12px;color:var(--navy);letter-spacing:.2px}
.brand-dot{width:9px;height:9px;border-radius:50%;background:var(--navy)}
.main-nav{position:absolute;right:60px;top:32px;display:flex;gap:23px;font-size:8.4px;letter-spacing:.1px}
.main-nav a{color:var(--ink);text-decoration:none;padding-bottom:5px}
.main-nav a.active{color:var(--navy);border-bottom:1px solid var(--navy)}
.hero{position:absolute;left:0;top:68px;width:734px;height:397px;overflow:hidden}
.hero-photo{position:absolute;inset:0;background:linear-gradient(110deg,var(--hero-b) 0%,var(--hero-a) 55%,#c9c8dc 100%)}
.hero-curve{position:absolute;left:0;bottom:0}
.hero-title{position:absolute;left:0;width:734px;top:134px;text-align:center;font-family:"Montserrat",sans-serif;font-weight:700;font-size:50px;color:var(--white);letter-spacing:.5px}
.hero-sub{position:absolute;left:0;width:734px;top:186px;text-align:center;font-size:13.5px;color:var(--white)}
.slide-arrow{position:absolute;top:170px;width:28px;height:28px;border-radius:50%;background:rgba(255,255,255,.18)}
.slide-arrow.prev{left:12px}.slide-arrow.next{right:12px}
.slide-arrow svg{position:absolute;left:8px;top:6px}
.welcome{position:absolute;left:0;top:478px;width:734px;text-align:center}
.welcome h1{font-weight:400;font-size:23px;color:var(--ink);margin-bottom:12px}
.welcome p{width:590px;margin:0 auto 13px;font-size:8.6px;line-height:16.5px;color:var(--muted)}
.services{position:absolute;left:0;top:673px;width:734px;height:316px;background:var(--band)}
.services h2{position:absolute;left:0;width:734px;top:36px;text-align:center;font-weight:400;font-size:22px;color:var(--ink)}
.service{position:absolute;top:92px;width:134px;margin-left:-67px;text-align:center}
.service-icon{width:78px;height:78px;margin:0 auto;border-radius:50%;background:var(--white);padding:3px}
.service-icon span{display:flex;align-items:center;justify-content:center;width:72px;height:72px;border-radius:50%;background:var(--navy)}
.service h3{margin-top:10px;font-weight:400;font-size:11.4px;letter-spacing:.2px;color:var(--ink);white-space:nowrap}
.service p{margin-top:6px;font-size:6.4px;line-height:12px;color:var(--muted)}
.read-more{position:absolute;left:50%;top:147px;margin-left:-40px;width:79px;height:23px;border:1px solid var(--navy);font-size:8.6px;line-height:21px;color:var(--navy);text-align:center}
.site-footer{position:absolute;left:0;top:989px;width:734px;height:211px;background:var(--navy);color:var(--footer-text)}
.site-footer h4{position:absolute;top:33px;font-weight:400;font-size:11.4px;color:var(--white);letter-spacing:.2px}
.links{position:absolute;top:59px;font-size:8.6px;line-height:19.4px;color:var(--footer-text)}
.divider{position:absolute;top:28px;width:1px;height:118px;background:rgba(255,255,255,.15)}
.contact{position:absolute;left:297px;top:59px;font-size:8.6px;line-height:16px}
.contact .row{display:flex;align-items:center;gap:8px;margin-top:3px}
.newsletter{position:absolute;left:473px;top:59px;font-size:8.6px}
.signup{display:flex;margin-top:8px}
.signup .field{width:135px;height:24px;background:var(--white);color:#b3b3b3;font-size:8px;line-height:24px;padding-left:9px}
.signup .btn{width:65px;height:24px;background:var(--navy-dark);color:var(--white);font-size:8.6px;line-height:24px;text-align:center}
.social{display:flex;gap:7px;margin-top:10px}
.social span{width:23px;height:23px;border-radius:50%;background:var(--white)}
.rule{position:absolute;left:60px;top:167px;width:614px;height:1px;background:rgba(255,255,255,.4)}
.copyright{position:absolute;left:60px;top:180px;font-size:8.6px;color:var(--footer-text)}
</style>
</head>
<body>
<header class="site-header">
  <div class="brand"><span class="brand-dot"></span>NORTHFIELD LENDING GROUP</div>
  <nav class="main-nav">
    <a class="active" href="#">HOME</a><a href="#">ABOUT</a><a href="#">TYPES OF MORTGAGES</a><a href="#">RENT TO OWN</a><a href="#">CONTACT US</a>
  </nav>
</header>

<section class="hero">
  <div class="hero-photo" role="img" aria-label="Hand holding a fan of banknotes in front of a house, tinted in lavender"></div>
  <div class="hero-title">RENT TO OWN A HOME</div>
  <div class="hero-sub">We provide mortgage lending and rent to own houses.</div>
  <div class="slide-arrow prev"><svg width="10" height="16" viewBox="0 0 10 16"><path d="M8 1 2 8l6 7" fill="none" stroke="#fff" stroke-width="1"/></svg></div>
  <div class="slide-arrow next"><svg width="10" height="16" viewBox="0 0 10 16"><path d="M2 1l6 7-6 7" fill="none" stroke="#fff" stroke-width="1"/></svg></div>
  <svg class="hero-curve" width="734" height="70" viewBox="0 0 734 70"><path d="M0 70 Q367 -34 734 70 Z" fill="#fff"/></svg>
</section>

<section class="welcome">
  <h1>Welcome to Northfield Lending Group</h1>
  <p>We know life sometimes delivers challenges and it can be hard to get back on track once you have dealt with challenges. Maybe you have been through a divorce, bankruptcy, consumer proposal, loss of job, work place injury, new to the country, self-employed or some credit related challenges that have you behind the eight ball? Are these challenges making it difficult to get a mortgage?</p>
  <p>None of these things has to bind you to a lifetime of renting. Want to start paying yourself first? We focus on rent to own in Pinecrest County and our Renting Program is a very viable option for those that can't get a mortgage today but are willing to work towards getting approved in the near future while living in their own home that they select. Homeownership is closer than you think.</p>
</section>

<section class="services">
  <h2>Our Services</h2>
  <div class="service" style="left:125px">
    <div class="service-icon"><span><svg width="30" height="26" viewBox="0 0 30 26" fill="none" stroke="#fff" stroke-width="1.6"><rect x="5" y="5" width="20" height="11" transform="rotate(-25 15 10)"/><circle cx="15" cy="10" r="2.5"/><path d="M10 22l5-4 5 4"/></svg></span></div>
    <h3>DOWN PAYMENT</h3>
    <p>We require a minimum down payment of $10,000 or 3.5% to 4% of total price of the home (whichever is larger).</p>
    <div class="read-more">READ MORE</div>
  </div>
  <div class="service" style="left:286px">
    <div class="service-icon"><span><svg width="30" height="24" viewBox="0 0 30 24" fill="none" stroke="#fff" stroke-width="1.6"><rect x="10" y="3" width="17" height="11" rx="1"/><path d="M10 7h17"/><path d="M3 13h9l3 3-3 4H5"/></svg></span></div>
    <h3>HOUSEHOLD INCOME</h3>
    <p>Steady, provable household income that can support the price of the home you would like.</p>
    <div class="read-more">READ MORE</div>
  </div>
  <div class="service" style="left:447px">
    <div class="service-icon"><span><svg width="26" height="28" viewBox="0 0 26 28" fill="none" stroke="#fff" stroke-width="1.6"><rect x="4" y="4" width="16" height="21" rx="1"/><path d="M9 3h6v3H9zM8 11h8M8 15h8M8 19h4"/><circle cx="19" cy="21" r="4" fill="#27215f"/><path d="M17 21l1.5 1.5L21 20"/></svg></span></div>
    <h3>CREDIT REPORT</h3>
    <p>We require a minimum down payment of $10,000 or 3.5% to 4% of total price of the home (whichever is larger).</p>
    <div class="read-more">READ MORE</div>
  </div>
  <div class="service" style="left:609px">
    <div class="service-icon"><span><svg width="28" height="28" viewBox="0 0 28 28" fill="none" stroke="#fff" stroke-width="1.6"><path d="M3 13 14 4l11 9M6 11v14h16V11"/><path d="M12 25v-7h5v7M8 15h3v3H8z"/></svg></span></div>
    <h3>SELECTING A HOUSE</h3>
    <p>We require a minimum down payment of $10,000 or 3.5% to 4% of total price of the home (whichever is larger).</p>
    <div class="read-more">READ MORE</div>
  </div>
</section>

<footer class="site-footer">
  <h4 style="left:60px">QUICK LINKS</h4>
  <div class="links" style="left:60px">Home<br>About<br>Types of mortgages<br>Rent to own</div>
  <div class="links" style="left:170px">Terms of Service<br>Privacy Policy<br>Contact Us</div>
  <div class="divider" style="left:260px"></div>
  <h4 style="left:297px">CONTACT INFO</h4>
  <div class="contact">
    Northfield Lending Group ,<br>lakeford,Northvale
    <div class="row"><svg width="9" height="9" viewBox="0 0 9 9"><rect width="9" height="9" rx="1.5" fill="#fff"/><path d="M2.5 2c0 3 1.5 4.5 4 5l.5-1.3-1.3-.7-.6.6C4.3 5.2 3.8 4.7 3.4 4l.6-.6-.7-1.3z" fill="#27215f"/></svg>+00 123 45 67 890</div>
    <div class="row"><svg width="10" height="8" viewBox="0 0 10 8"><rect width="10" height="8" fill="#fff"/><path d="M0 0l5 4 5-4" fill="none" stroke="#27215f"/></svg>info@northfieldlending.ca</div>
  </div>
  <div class="divider" style="left:445px"></div>
  <h4 style="left:473px">SIGN UP FOR NEWSLETTERS</h4>
  <div class="newsletter">
    Please sign up here for latest news
    <div class="signup"><div class="field">EMAIL ADDRESS</div><div class="btn">SUBSCRIBE</div></div>
    <div class="social"><span></span><span></span><span></span><span></span></div>
  </div>
  <div class="rule"></div>
  <div class="copyright">© 2017 NORTHFIELD LENDING GROUP.&nbsp; All right reserved . Term of Use</div>
</footer>
</body>
</html>
```